Pebble Pete''s Funhouse Website Revamp

We have a children's entertainment center that hasn't changed in 20 years and the site looks like it was created 20 years ago. We need a new, modern, clean site that pops. Attached is the new logo that should be used as a style guide.

Current site is: www.pebblepetesfun-example.com

Thanks!
Updates

Designers, thank you all for the amazing work. It was exciting to be able to go through and see all the creativity that came in. I have decided on a design but wanted to share my thanks and appreciation for your time. Warm regards, Morris

Target Market(s)

Mothers with children in the 2 - 14 range.

Industry/Entity Type

Entertainment

```html
<!DOCTYPE html>
<html lang="en">
<head>
<meta charset="utf-8">
<title>Pebble Pete's Funhouse</title>
<link rel="stylesheet" href="https://fonts.googleapis.com/css2?family=Open+Sans:wght@400;600&family=Sriracha&family=Crimson+Text:ital@0;1&family=Arimo&display=swap">
<style>
:root{
  --sky-top:#bfe3f2;
  --sky-mid:#dff1e4;
  --page-white:#ffffff;
  --page-tint:#f1fafb;
  --orange:#ef6a2a;
  --orange-light:#f58a4a;
  --phone-red:#e24b2e;
  --teal:#17a3b4;
  --teal-dark:#0c8f9e;
  --blue-btn:#2cb2e6;
  --blue-btn-light:#6fd0f3;
  --slider-text:#2f8fb5;
  --body-grey:#5a5a5a;
  --list-grey:#666666;
  --footer-text:#2a2a2a;
  --grass:#8ccf6a;
}
*{box-sizing:border-box;margin:0;padding:0}
html,body{width:998px;height:1200px;overflow:hidden;background:var(--page-white)}
.page{position:relative;width:998px;height:1200px;overflow:hidden;
  background:linear-gradient(180deg,var(--sky-top) 0,var(--sky-mid) 420px,#f4fbf7 560px,var(--page-white) 650px,var(--page-tint) 1000px);
  font-family:'Arimo',Arial,sans-serif}
.abs{position:absolute}
.art{position:absolute}

/* scenery: soft tonal fields where the cartoon art sits */
.tree-left{left:0;top:0;width:130px;height:190px;background:radial-gradient(ellipse at 20% 35%,rgba(150,205,110,.75),rgba(190,228,160,.45) 55%,rgba(190,228,160,0) 75%)}
.tree-right{right:0;top:0;width:140px;height:210px;background:radial-gradient(ellipse at 80% 35%,rgba(150,205,110,.75),rgba(190,228,160,.45) 55%,rgba(190,228,160,0) 75%)}
.koala{left:0;top:185px;width:134px;height:305px;background:radial-gradient(ellipse at 45% 40%,rgba(135,135,140,.7),rgba(150,150,155,.35) 50%,rgba(150,150,155,0) 72%)}
.monkey{left:888px;top:195px;width:110px;height:185px;background:radial-gradient(ellipse at 50% 45%,rgba(226,145,59,.7),rgba(240,190,120,.35) 50%,rgba(240,190,120,0) 72%)}

/* header */
.call{left:122px;top:37px;display:flex;gap:14px}
.call-icon{width:24px;height:24px;border-radius:4px;background:var(--phone-red);display:flex;align-items:center;justify-content:center}
.call-label{font-family:'Crimson Text',Georgia,serif;font-size:13px;color:#222;line-height:1}
.call-number{font-family:'Crimson Text',Georgia,serif;font-size:20px;color:var(--phone-red);line-height:1.1;margin-top:2px}
.social{left:786px;top:34px;display:flex;gap:4px}
.social span{width:22px;height:22px;display:block}
.social .s1{background:#3b5c99}.social .s2{background:#45b3e3}.social .s3{background:#d9472f}.social .s4{background:#cc2b20}

.nav{left:110px;top:78px;width:779px;height:50px;background:linear-gradient(180deg,var(--orange-light),var(--orange));box-shadow:0 3px 4px rgba(0,0,0,.18)}
.nav a{position:absolute;top:0;line-height:48px;color:#fff;text-decoration:none;font-family:'Open Sans',Arial,sans-serif;font-size:14px}
.brand{position:absolute;left:0;width:779px;top:0;text-align:center;line-height:48px;color:#fff;font-family:'Open Sans',Arial,sans-serif;font-weight:600;font-size:15px;pointer-events:none}

/* slider */
.slider{left:110px;top:140px;width:779px;height:396px;background:var(--page-white)}
.slide-photo{left:133px;top:165px;width:530px;height:345px;background:linear-gradient(135deg,#7fb3d6 0,#6aa84f 35%,#2f8f6a 55%,#d9a52c 75%,#4c7a3a 100%)}
.slide-panel{left:660px;top:165px;width:204px;height:343px;border:1px solid #e8e8e8;border-left:none}
.slide-title{left:668px;top:204px;width:190px;font-family:'Sriracha',cursive;font-style:italic;font-size:16px;line-height:22px;color:var(--orange);white-space:nowrap;overflow:hidden}
.slide-text{left:670px;top:242px;width:186px;font-family:'Crimson Text',Georgia,serif;font-style:italic;font-size:10px;line-height:18px;color:var(--slider-text)}
.btn-blue{left:674px;top:408px;width:137px;height:33px;border-radius:3px;background:linear-gradient(180deg,var(--blue-btn-light),var(--blue-btn));color:#fff;font-family:'Crimson Text',Georgia,serif;font-style:italic;font-size:15px;text-align:center;line-height:33px}
.dots{left:790px;top:489px;display:flex;gap:6px}
.dots span{width:10px;height:10px;border-radius:50%;background:#8c8c8c}
.dots span.active{background:var(--blue-btn)}

/* welcome */
.welcome{left:0;width:998px;top:536px;text-align:center;font-family:'Sriracha',cursive;font-style:italic;font-size:23px;color:var(--orange)}
.intro{left:122px;width:760px;top:580px;text-align:center;font-size:10.5px;line-height:26.5px;color:var(--body-grey)}

/* columns */
.col-head{top:698px;font-family:'Sriracha',cursive;font-style:italic;font-size:17px;color:var(--teal);white-space:nowrap}
.ideal-list{left:116px;top:742px;list-style:none}
.ideal-list li{height:28px;line-height:24px;font-family:'Crimson Text',Georgia,serif;font-style:italic;font-size:11px;color:var(--list-grey);display:flex;align-items:center;gap:10px}
.ideal-list svg{flex:none}
.distances{left:374px;top:742px;width:252px;font-family:'Crimson Text',Georgia,serif;font-style:italic;font-size:10.5px;line-height:26.5px;color:var(--list-grey)}
.btn-orange{left:369px;top:919px;width:105px;height:34px;border-radius:4px;background:linear-gradient(180deg,var(--orange-light),var(--orange));color:#fff;font-family:'Sriracha',cursive;font-style:italic;font-size:13px;line-height:34px;text-align:center}

.offers{left:652px;top:710px;width:237px;height:242px;background:linear-gradient(180deg,#24b7c4,var(--teal-dark))}
.offers-title{left:680px;top:722px;width:200px;font-family:'Sriracha',cursive;font-style:italic;line-height:1}
.offers-title .o1{display:block;font-size:27px;color:#fff;margin-left:30px}
.offers-title .o2{display:block;font-size:46px;color:#f4e33a;margin-left:0}
.offers-art{left:674px;top:832px;width:188px;height:104px;border-radius:5px;background:linear-gradient(180deg,#4cbf4c,#8fcf3c)}
.offers-more{left:687px;top:912px;font-family:'Crimson Text',Georgia,serif;font-size:9px;color:#fff}

/* footer */
.footer{left:0;top:1008px;width:998px;height:192px;background:linear-gradient(180deg,#a9dcf2 0,#cbeaf4 90px,#d8f0da 140px,var(--grass) 192px)}
.footer-cartoon{left:10px;top:995px;width:210px;height:190px;background:radial-gradient(ellipse at 45% 50%,rgba(123,135,148,.6),rgba(170,180,190,.3) 50%,rgba(170,180,190,0) 72%)}
.footer-mascot{left:760px;top:1045px;width:150px;height:155px;background:radial-gradient(ellipse at 50% 50%,rgba(90,106,134,.65),rgba(227,80,43,.35) 50%,rgba(242,193,46,0) 72%)}
.footer-links{left:0;width:998px;top:1063px;text-align:center;font-family:'Crimson Text',Georgia,serif;font-style:italic;font-size:10px;color:var(--footer-text);letter-spacing:-.1px}
.footer-links span{margin:0 4px}
.footer-info{left:0;width:998px;top:1095px;text-align:center;font-family:'Crimson Text',Georgia,serif;font-size:8px;color:var(--footer-text)}
.footer-copy{left:0;width:998px;top:1124px;text-align:center;font-family:'Crimson Text',Georgia,serif;font-size:8.5px;color:var(--footer-text)}
</style>
</head>
<body>
<div class="page">

  <div class="art tree-left" role="img" aria-label="Cartoon tree foliage"></div>
  <div class="art tree-right" role="img" aria-label="Cartoon tree foliage"></div>
  <div class="art koala" role="img" aria-label="Cartoon koala clinging to a tree branch"></div>
  <div class="art monkey" role="img" aria-label="Cartoon monkey hanging from a vine"></div>

  <header>
    <div class="abs call">
      <div class="call-icon">
        <svg width="14" height="14" viewBox="0 0 24 24"><path fill="#fff" d="M6.6 10.8a15 15 0 0 0 6.6 6.6l2.2-2.2c.3-.3.7-.4 1-.2 1.1.4 2.3.6 3.6.6.6 0 1 .4 1 1V20c0 .6-.4 1-1 1A17 17 0 0 1 3 4c0-.6.4-1 1-1h3.5c.6 0 1 .4 1 1 0 1.2.2 2.4.6 3.6.1.3 0 .7-.2 1z"/></svg>
      </div>
      <div>
        <div class="call-label">Call Us Today:</div>
        <div class="call-number">80055501234</div>
      </div>
    </div>

    <div class="abs social" aria-label="Social links">
      <span class="s1"></span><span class="s2"></span><span class="s3"></span><span class="s4"></span>
    </div>

    <nav class="abs nav">
      <a style="left:30px">Home</a>
      <a style="left:106px">Attractions</a>
      <a style="left:215px">Parties</a>
      <div class="brand">Pebble Pete's Funhouse</div>
      <a style="left:521px">Pricing</a>
      <a style="left:602px">Directions</a>
      <a style="left:702px">Contact</a>
    </nav>
  </header>

  <section>
    <div class="abs slider"></div>
    <div class="art slide-photo" role="img" aria-label="Photo of children riding a dragon roller coaster"></div>
    <div class="abs slide-panel"></div>
    <svg class="abs" style="left:600px;top:165px" width="70" height="345" viewBox="0 0 70 345">
      <path fill="#fff" d="M70 0 L58 0 C40 15 30 40 45 60 C25 80 28 110 48 125 C30 150 32 180 50 195 C28 215 30 250 48 268 C20 285 12 320 14 345 L70 345 Z"/>
    </svg>
    <div class="abs slide-title">Pebble Pete's is ideal for</div>
    <p class="abs slide-text">Pebble Pete's Funhouse is the Valley's #1 indoor amusement park for young kids. We cater exclusively to children from infants to around 11 years old. Our climate controlled fun center offers a unique mix of seven different amusement park rides. Pebble Pete's also makes its own pizza with fresh ingredients that will satisfy appetite........</p>
    <div class="abs btn-blue">READ MORE</div>
    <div class="abs dots"><span class="active"></span><span></span><span></span><span></span></div>
  </section>

  <section>
    <h1 class="abs welcome">Welcome To The Funhouse!</h1>
    <p class="abs intro">Pebble Pete's Funhouse is the Valley's #1 indoor amusement park for young kids. We cater exclusively to children from infants to around 11 years old. Our climate controlled fun center offers a unique mix of seven different amusement park rides. Pebble Pete's also makes its own pizza with fresh ingredients that will satisfy any families appetite. Our family fun center is a fun, affordable and exciting birthday party place.</p>
  </section>

  <section>
    <h2 class="abs col-head" style="left:112px">Pebble Pete's is ideal for:</h2>
    <ul class="abs ideal-list">
      <li><svg width="16" height="8" viewBox="0 0 16 8"><path d="M0 4h14M10 1l4 3-4 3" stroke="#ef6a2a" stroke-width="1.2" fill="none"/></svg>Kids Birthday Parties</li>
      <li><svg width="16" height="8" viewBox="0 0 16 8"><path d="M0 4h14M10 1l4 3-4 3" stroke="#ef6a2a" stroke-width="1.2" fill="none"/></svg>Play Group Location</li>
      <li><svg width="16" height="8" viewBox="0 0 16 8"><path d="M0 4h14M10 1l4 3-4 3" stroke="#ef6a2a" stroke-width="1.2" fill="none"/></svg>Family Night Activities</li>
      <li><svg width="16" height="8" viewBox="0 0 16 8"><path d="M0 4h14M10 1l4 3-4 3" stroke="#ef6a2a" stroke-width="1.2" fill="none"/></svg>Kids Field Trip Location</li>
      <li><svg width="16" height="8" viewBox="0 0 16 8"><path d="M0 4h14M10 1l4 3-4 3" stroke="#ef6a2a" stroke-width="1.2" fill="none"/></svg>Grandparents Day Out with the Kids</li>
      <li><svg width="16" height="8" viewBox="0 0 16 8"><path d="M0 4h14M10 1l4 3-4 3" stroke="#ef6a2a" stroke-width="1.2" fill="none"/></svg>Fun things to do with Kids</li>
      <li><svg width="16" height="8" viewBox="0 0 16 8"><path d="M0 4h14M10 1l4 3-4 3" stroke="#ef6a2a" stroke-width="1.2" fill="none"/></svg>Large Groups and Large Parties</li>
      <li><svg width="16" height="8" viewBox="0 0 16 8"><path d="M0 4h14M10 1l4 3-4 3" stroke="#ef6a2a" stroke-width="1.2" fill="none"/></svg>Off Track Activities for Children</li>
      <li><svg width="16" height="8" viewBox="0 0 16 8"><path d="M0 4h14M10 1l4 3-4 3" stroke="#ef6a2a" stroke-width="1.2" fill="none"/></svg>Rainy Day Activities</li>
    </ul>

    <h2 class="abs col-head" style="left:366px">Driving distance to Pebble Pete's:</h2>
    <p class="abs distances">Cedar Hollow 8mi; Maple Ridge 3mi; Stonebrook 8mi; Willow Bend 3mi; Fernwood 9mi; Oak Landing 10mi; Pine Harbor 6mi; Birchfield 5mi; Elm Crossing 4mi; Aspen Vale 3mi; Clearwater Glen 8mi; Hillcrest Park 23mi; Juniper Falls 28mi; Marble Creek 33mi; Foxmoor 22mi; Ravenford 36mi; Summit Lakes 32mi</p>
    <div class="abs btn-orange">READ MORE</div>

    <div class="abs offers"></div>
    <div class="abs offers-title"><span class="o1">ONLINE</span><span class="o2">OFFERS</span></div>
    <div class="art offers-art" role="img" aria-label="Illustration of gold coins on a stack of banknotes"></div>
    <div class="abs offers-more">READ MORE</div>
  </section>

  <footer>
    <div class="art footer" role="img" aria-label="Cartoon sky with clouds over green hills"></div>
    <div class="art footer-cartoon" role="img" aria-label="Cartoon cat chasing a mouse"></div>
    <div class="art footer-mascot" role="img" aria-label="Cartoon gorilla mascot holding a leaf"></div>
    <div class="abs footer-links">HOME PAGE<span>|</span>THE PEBBLE CAFE<span>|</span>ATTRACTIONS<span>|</span>PARTIES<span>|</span>PRICING<span>|</span>GROUP OUTINGS<span>|</span>DIRECTIONS<span>|</span>CONTACT US</div>
    <div class="abs footer-info">120 MAPLE GROVE AVENUE IN BROOKVALE CALL 555-010-2222. HOURS: MON-THU 11AM-9PM, FRI 11AM-10PM, SAT 10AM-10PM</div>
    <div class="abs footer-copy">CopyRight 2014 Pebble Pete's. All Right Reseved.</div>
  </footer>

</div>
</body>
</html>
```